Finding the Root: Reason in Clinical Choice-Crafting

I'd like a cover that looks like it would fit on the shelf next to "The Illness Mirage" by Corwin Talley, "The Close of Forgetting" by Hugh Marchetti, "Meal Mend" by Paul Grieve, "The Energy Restart Plan" by Oscar Pemberley or "The Gland Restart Plan" by the same or "The Cortex Restart Plan" by the same ... either text only (with some interesting fonts that make the title stand out, and the subtitle smaller) or a relevant image, though I'm not entirely sure what that would be since this is a book about big-picture medical decision making.
Author name is Dr Tessa Morrow, NMD
I'll eventually request an e-book, paperback, and audio cover from the winner...

Target Market(s)

practicing physicians

Industry/Entity Type

medicine

Requirements
Must have
• look similar to other books in the genre

```html
<!DOCTYPE html>
<html lang="en">
<head>
<meta charset="utf-8">
<title>Finding the Root — Cover Options</title>
<link rel="stylesheet" href="https://fonts.googleapis.com/css2?family=Cinzel:wght@400;500;600&family=Josefin+Sans:wght@400;500&display=swap">
<style>
  :root {
    --backdrop: #bdbdbd;
    --paper: #fdfcf6;
    --ink: #1c1c1c;
    --gold: #c9981f;
    --gold-line: #d2a43a;
    --fruit-green: #dfe9c4;
    --fruit-orange: #f6d49a;
    --fruit-pink: #f3c6b8;
    --fruit-lime: #e5ecb8;
    --ornament-cream: #f5eedc;
    --ornament-gold: #e6d3a4;
  }
  * { margin: 0; padding: 0; box-sizing: border-box; }
  html, body { width: 1200px; height: 868px; overflow: hidden; }
  body {
    background: var(--backdrop);
    position: relative;
  }
  .cover {
    position: absolute;
    top: 128px;
    width: 405px;
    height: 624px;
    background: var(--paper);
    overflow: hidden;
    box-shadow: 0 6px 18px rgba(0,0,0,0.18);
  }
  .cover--fruit { left: 153px; }
  .cover--compass { left: 677px; }

  .art { position: absolute; left: 0; width: 100%; }
  .art--fruit-top {
    top: 0; height: 170px;
    background:
      radial-gradient(circle at 30% 30%, var(--fruit-pink) 0 14%, transparent 30%),
      radial-gradient(circle at 60% 8%, var(--fruit-orange) 0 12%, transparent 26%),
      radial-gradient(circle at 86% 28%, var(--fruit-lime) 0 13%, transparent 28%),
      linear-gradient(180deg, var(--fruit-green) 0%, var(--paper) 100%);
  }
  .art--fruit-bottom {
    bottom: 0; height: 200px;
    background:
      radial-gradient(circle at 18% 30%, #f8eab0 0 12%, transparent 26%),
      radial-gradient(circle at 65% 25%, var(--fruit-lime) 0 14%, transparent 30%),
      radial-gradient(circle at 88% 12%, var(--fruit-pink) 0 9%, transparent 20%),
      radial-gradient(circle at 22% 80%, var(--fruit-pink) 0 12%, transparent 26%),
      radial-gradient(circle at 52% 78%, var(--fruit-lime) 0 14%, transparent 30%),
      linear-gradient(0deg, #f2f3e2 0%, var(--paper) 100%);
  }
  .art--compass {
    top: 262px; height: 130px;
    background:
      radial-gradient(ellipse at 50% 50%, var(--ornament-gold) 0 10%, transparent 30%),
      linear-gradient(90deg, var(--paper) 0%, var(--ornament-cream) 40%, var(--ornament-cream) 60%, var(--paper) 100%);
  }

  .title {
    position: absolute;
    left: 0; width: 100%;
    text-align: center;
    font-family: "Cinzel", serif;
    font-weight: 500;
    line-height: 1;
  }
  .title__lead {
    display: block;
    font-size: 42px;
    color: var(--ink);
    letter-spacing: 0.5px;
  }
  .title__key {
    display: block;
    font-size: 90px;
    color: var(--gold);
    margin-top: 14px;
    letter-spacing: 1px;
  }
  .cover--fruit .title { top: 86px; }
  .cover--compass .title { top: 58px; }

  .subtitle {
    position: absolute;
    left: 46px; right: 46px;
    border-top: 1px solid var(--gold-line);
    border-bottom: 1px solid var(--ink);
    padding: 14px 0 12px;
    text-align: center;
    font-family: "Josefin Sans", sans-serif;
    font-weight: 400;
    line-height: 1.2;
  }
  .subtitle__line { display: block; font-size: 22px; color: var(--ink); letter-spacing: 1px; }
  .subtitle__line--accent { color: var(--gold); font-size: 23px; }
  .cover--fruit .subtitle { top: 272px; }
  .cover--compass .subtitle { top: 420px; }

  .author {
    position: absolute;
    left: 0; width: 100%;
    text-align: center;
    font-family: "Cinzel", serif;
    font-weight: 600;
    font-size: 17px;
    color: var(--ink);
    letter-spacing: 0.5px;
  }
  .cover--fruit .author { top: 392px; }
  .cover--compass .author { top: 562px; }
</style>
</head>
<body>
  <section class="cover cover--fruit">
    <div class="art art--fruit-top" role="img" aria-label="Photograph of fresh fruit slices: grapefruit, orange and kiwi on a pale background"></div>
    <div class="art art--fruit-bottom" role="img" aria-label="Photograph of fruit slices and leaves: lemon, kiwi, papaya and guava"></div>
    <h1 class="title">
      <span class="title__lead">FINDING THE</span>
      <span class="title__key">ROOT</span>
    </h1>
    <p class="subtitle">
      <span class="subtitle__line">REASON IN CLINICAL</span>
      <span class="subtitle__line subtitle__line--accent">CHOICE-CRAFTING</span>
    </p>
    <p class="author">DR TESSA MORROW, NMD</p>
  </section>

  <section class="cover cover--compass">
    <h1 class="title">
      <span class="title__lead">FINDING THE</span>
      <span class="title__key">ROOT</span>
    </h1>
    <div class="art art--compass" role="img" aria-label="Gold compass-star ornament over a faint flowing wave of dots"></div>
    <p class="subtitle">
      <span class="subtitle__line">REASON IN CLINICAL</span>
      <span class="subtitle__line subtitle__line--accent">CHOICE-CRAFTING</span>
    </p>
    <p class="author">DR TESSA MORROW, NMD</p>
  </section>
</body>
</html>
```